Buch-/eBook-Cover für Traumatherapeutin
Zielgruppe
Ich bin Traumatherapeutin und schreibe ein Buch zum Thema Trauma bearbeiten.
Meine Zielgruppe sucht Heilung, Genesung, Selbstliebe etc.
Aufgabenstellung
Buchcover
Bitte erstell mir ein modernes positives inspirierendes Buchcover mit dem
Titel: 'Morgenlicht NEU entdecken“
Untertitel: „Spüre den Mut der ganz in dir wohnt“
Dr. Mira Kessow
Ich hätte gerne ein modernes Buch, das entweder einen Bezug zum Thema Trauma hat oder aber einfach stylische Schriftzüge. Bin aber auch offen für andere Vorschläge.
Dunkelblau, weiß und türkis oder auch rosa mag ich ganz gerne. Wobei Dunkelblau, weiß und türkis meine Favoriten sind und mit rosa höchstens kleinere Akzente gesetzt werden sollten.
Das Buchcover soll modern sein und direkt ansprechen. Gerne eine originelle Lösung, oder etwas Besonderes, etwas das Tiefe ausdrückt, oder man mehrmals hinsehen muss um etwas zu erkennen oder etwas das mehr Interpretationsspielraum lässt.
Gerne auch viel weiß, zumindest heller und nicht zu dunkel. Stylish, aber nicht überfrachtet.
Schreib mich gerne an, wenn du Fragen hast.
Ich habe mal zwei Beispiel von Typolösungen angehängt, die ich ganz cool fände.
Ich freue mich auf deine Ideen :-)
Ganz liebe Grüße
Mira

```html
<!DOCTYPE html>
<html lang="de">
<head>
<meta charset="utf-8">
<title>Morgenlicht NEU entdecken – Buchcover</title>
<link rel="stylesheet" href="https://fonts.googleapis.com/css2?family=Bebas+Neue&family=Open+Sans:ital,wght@0,400;1,400&family=Sacramento&display=swap">
<style>
  :root {
    --bg-pink: #d8a6c2;
    --bg-light: #c4d9dc;
    --bg-teal: #a8d9d3;
    --ink-purple: #5a3a92;
    --paper-white: #ffffff;
  }
  html, body {
    margin: 0;
    padding: 0;
    width: 858px;
    height: 1200px;
    overflow: hidden;
    background: var(--paper-white);
  }
  .book-cover {
    display: block;
    width: 858px;
    height: 1200px;
  }
  .author-name {
    font-family: "Open Sans", sans-serif;
    font-size: 17px;
    fill: var(--paper-white);
  }
  .title-script {
    font-family: "Sacramento", cursive;
    fill: var(--ink-purple);
    stroke: var(--ink-purple);
    stroke-width: 1.2;
  }
  .title-bold {
    font-family: "Bebas Neue", sans-serif;
    font-size: 150px;
  }
  .title-bold--shadow { fill: var(--ink-purple); }
  .title-bold--face { fill: var(--paper-white); }
  .subtitle {
    font-family: "Open Sans", sans-serif;
    font-style: italic;
    font-size: 17px;
    fill: var(--ink-purple);
  }
  .ornament-area {
    fill: var(--paper-white);
    opacity: 0.16;
  }
</style>
</head>
<body>
<svg class="book-cover" viewBox="0 0 587 822" xmlns="http://www.w3.org/2000/svg" aria-label="Buchcover Morgenlicht NEU entdecken von Dr. Mira Kessow">
  <defs>
    <linearGradient id="cover-gradient" x1="0" y1="0" x2="0.3" y2="1">
      <stop offset="0" stop-color="var(--bg-light)"/>
      <stop offset="0.6" stop-color="var(--bg-teal)"/>
      <stop offset="1" stop-color="var(--bg-teal)"/>
    </linearGradient>
    <radialGradient id="pink-accent" cx="0" cy="0" r="0.45">
      <stop offset="0" stop-color="var(--bg-pink)" stop-opacity="0.85"/>
      <stop offset="1" stop-color="var(--bg-pink)" stop-opacity="0"/>
    </radialGradient>
  </defs>

  <rect class="cover-background" x="0" y="0" width="587" height="822" fill="url(#cover-gradient)"/>
  <rect class="cover-accent" x="0" y="0" width="587" height="822" fill="url(#pink-accent)"/>

  <g class="ornament-top" role="img" aria-label="Gestrichelte Herzlinie als Dekoration oben rechts">
    <ellipse class="ornament-area" cx="460" cy="140" rx="95" ry="70"/>
  </g>
  <g class="ornament-bottom" role="img" aria-label="Gestrichelte Herzlinie als Dekoration unten links">
    <ellipse class="ornament-area" cx="145" cy="645" rx="95" ry="70"/>
  </g>

  <text class="author-name" x="293" y="64" text-anchor="middle">Dr. Mira Kessow</text>

  <g class="book-title">
    <text class="title-script" x="40" y="300" font-size="78" textLength="370" lengthAdjust="spacingAndGlyphs">Morgenlicht</text>
    <text class="title-bold title-bold--shadow" x="296" y="448" text-anchor="middle">NEU</text>
    <text class="title-bold title-bold--face" x="302" y="443" text-anchor="middle">NEU</text>
    <text class="title-script" x="222" y="502" font-size="64" textLength="322" lengthAdjust="spacingAndGlyphs">entdecken</text>
  </g>

  <g class="book-subtitle">
    <text class="subtitle" x="527" y="555" text-anchor="end">Spüre den Mut der ganz</text>
    <text class="subtitle" x="527" y="580" text-anchor="end">in dir wohnt</text>
  </g>
</svg>
</body>
</html>
```